OBK Farcoast Logistics Limited

We need the buissnes card to be very exclusive. As we are all young in our company. We need this to be the gate to make our clients feel deep interest for us.

We are focused in as International Trade advisors, and our products go from Oil Tanker Ships to Rubber balls for dogs.

Our Slogan is Linking Far Coasts.
And our main marketing will be through Internet.

We were stablished in 2009 In Mexico and we also have offices in Hong Kong.
We have representatives in China and Europe.

Target Market(s)

Is every company or Individual that wants to develop an International Project or product development or Logistic service of Goods and people.
Some of our current projects are Ship Brokerage, Mine Brokerage, Real State and Product Pormotional development.

Industry/Entity Type

It Company

Requirements
Must have
• Our Logo and slogan, and make the card accoriding to the logo.
Nice to have
• Our Colors

```html
<!DOCTYPE html>
<html lang="en">
<head>
<meta charset="utf-8">
<title>Business Card – Front and Back</title>
<link rel="stylesheet" href="https://fonts.googleapis.com/css2?family=Open+Sans:wght@400;600;700&display=swap">
<style>
  :root {
    --backdrop: #e9e6e1;
    --card: #ffffff;
    --navy: #2b46a0;
    --sky: #1f8ac8;
    --leaf: #7cc242;
    --ink: #3d3d3d;
    --on-navy: #ffffff;
    --shadow: rgba(0, 0, 0, 0.18);
  }
  * { box-sizing: border-box; margin: 0; padding: 0; }
  html, body {
    width: 1200px; height: 720px; overflow: hidden;
    background: var(--backdrop);
    font-family: "Open Sans", Arial, sans-serif;
  }
  .stage {
    position: relative; width: 1200px; height: 720px;
    display: flex; align-items: center; justify-content: center; gap: 40px;
  }
  .card {
    position: relative; width: 540px; height: 309px;
    background: var(--card);
    box-shadow: 0 6px 18px var(--shadow);
    overflow: hidden;
  }
  .card-art { position: absolute; inset: 0; }

  /* Front side */
  .brand {
    position: absolute; left: 48px; top: 92px;
    display: flex; flex-direction: column; align-items: flex-start;
  }
  .brand-row { display: flex; align-items: center; gap: 12px; }
  .brand-dot { width: 40px; height: 40px; border-radius: 50%; background: var(--sky); }
  .brand-name {
    font-weight: 700; font-size: 52px; line-height: 1;
    color: var(--leaf); letter-spacing: 2px;
  }
  .brand-slogan { margin-top: 8px; font-size: 13px; color: var(--sky); }

  .contact {
    position: absolute; right: 26px; top: 26px;
    color: var(--on-navy); text-align: right;
  }
  .contact-name { font-weight: 700; font-size: 17px; line-height: 1.1; }
  .contact-title { font-size: 11px; margin-bottom: 16px; }
  .contact-list { list-style: none; font-size: 12.5px; line-height: 1.5; }
  .contact-list li { display: flex; justify-content: flex-end; align-items: center; gap: 6px; }
  .contact-list svg { width: 11px; height: 11px; fill: var(--on-navy); }
  .contact-address { margin-top: 12px; font-size: 12px; line-height: 1.35; }

  /* Back side */
  .card-back { display: flex; flex-direction: column; align-items: center; }
  .mark { margin-top: 62px; display: flex; align-items: center; gap: 16px; }
  .mark-dot { width: 58px; height: 58px; border-radius: 50%; background: var(--sky); }
  .mark-name { font-weight: 700; font-size: 72px; line-height: 1; color: var(--navy); letter-spacing: 3px; }
  .back-slogan { margin-top: 38px; font-size: 21px; color: var(--navy); }
  .back-url { margin-top: 4px; font-size: 19px; color: var(--ink); letter-spacing: 3px; }
</style>
</head>
<body>
<main class="stage">
  <section class="card card-front" aria-label="Business card front">
    <svg class="card-art" viewBox="0 0 540 309" aria-hidden="true">
      <circle cx="512" cy="32" r="266" fill="var(--leaf)"/>
      <circle cx="519" cy="22" r="261" fill="var(--card)"/>
      <circle cx="517" cy="22" r="257" fill="var(--sky)"/>
      <circle cx="527" cy="12" r="247" fill="var(--navy)"/>
    </svg>

    <div class="brand">
      <div class="brand-row">
        <span class="brand-dot"></span>
        <span class="brand-name">OBK</span>
      </div>
      <p class="brand-slogan">Linking Far Coasts</p>
    </div>

    <div class="contact">
      <p class="contact-name">Your Name</p>
      <p class="contact-title">Title</p>
      <ul class="contact-list">
        <li><svg viewBox="0 0 12 12"><path d="M2.5 1l2 2.2-1 1.3c.7 1.5 2 2.8 3.5 3.5l1.3-1 2.2 2-1.3 1.8C5 10.5 1.5 7 1 2.3z"/></svg>123-456-0789</li>
        <li><svg viewBox="0 0 12 12"><path d="M3.5 0h5a1 1 0 0 1 1 1v10a1 1 0 0 1-1 1h-5a1 1 0 0 1-1-1V1a1 1 0 0 1 1-1zm.5 1.5v7.5h4V1.5zm2 8.5a.7.7 0 1 0 0 1.4.7.7 0 0 0 0-1.4z"/></svg>123-456-0789</li>
        <li><svg viewBox="0 0 12 12"><path d="M0 2.5h12v7H0zm1 .8v.4l5 3.2 5-3.2v-.4z"/></svg>info@farcoastobk.com</li>
        <li><svg viewBox="0 0 12 12"><path d="M6 0a6 6 0 1 0 0 12A6 6 0 0 0 6 0zm0 1c.8 0 1.6 1.9 1.7 4.5H4.3C4.4 2.9 5.2 1 6 1zM1 6.5h2.3c0 1.6.3 3 .8 4A5 5 0 0 1 1 6.5zm0-1a5 5 0 0 1 3.1-4c-.5 1-.8 2.4-.8 4zm5 5.5c-.8 0-1.6-1.9-1.7-4.5h3.4C7.6 9.1 6.8 11 6 11zm1.9-.5c.5-1 .8-2.4.8-4H11a5 5 0 0 1-3.1 4zm.8-5c0-1.6-.3-3-.8-4a5 5 0 0 1 3.1 4z"/></svg>www.farcoastobk.com</li>
      </ul>
      <p class="contact-address">Street Name, City Name<br>State Zip Code</p>
    </div>
  </section>

  <section class="card card-back" aria-label="Business card back">
    <div class="mark">
      <span class="mark-dot"></span>
      <span class="mark-name">OBK</span>
    </div>
    <p class="back-slogan">Linking Far Coasts</p>
    <p class="back-url">www.farcoastobk.com</p>
  </section>
</main>
</body>
</html>
```